E learning Platform for privacy

Current website is as below and its more of a shell.
I need someone to take the text and content and design it properly.
https://study.vornaquill.com/

After that, design has to be implemented with elementor and wordpress
https://elementor.com/

```html
<!DOCTYPE html>
<html lang="en">
<head>
<meta charset="utf-8">
<title>Vorna Learning Centre</title>
<link href="https://fonts.googleapis.com/css2?family=Oswald:wght@400;500;600&family=Poppins:wght@300;400;500&display=swap" rel="stylesheet">
<style>
:root{
  --orange:#e85c2a;
  --orange-soft:#f3c4ae;
  --dark:#2b2b2b;
  --text:#555;
  --line:#e6e6e6;
  --white:#fff;
  --head:"Oswald",sans-serif;
  --body:"Poppins",sans-serif;
}
*{margin:0;padding:0;box-sizing:border-box}
html,body{width:1200px;height:4386px;overflow:hidden}
body{position:relative;font-family:var(--body);color:var(--text);background:var(--white)}
.abs{position:absolute}
.h{font-family:var(--head);font-weight:600;color:var(--dark);text-transform:uppercase;line-height:1.15}
.btn-outline{position:absolute;display:flex;align-items:center;justify-content:center;gap:8px;border:1px solid var(--orange);font-size:14px;color:var(--dark);background:#fff}
.btn-outline svg{width:8px;height:10px}
/* hero */
.hero{top:0;left:0;width:1200px;height:599px;overflow:hidden}
.hero-photo{position:absolute;inset:0;background:linear-gradient(120deg,#c98a5a 0%,#d9b58d 45%,#8c7a6a 75%,#e9e3dc 100%)}
.logo{position:absolute;display:flex;flex-direction:column;align-items:center}
.logo .name{font-family:var(--body);font-weight:500;font-size:38px;letter-spacing:4px;color:#fff;line-height:1}
.logo .sub{font-size:9px;letter-spacing:6px;color:#fff;margin-top:4px}
.nav{top:60px;left:388px;width:497px;height:63px;background:#fff;display:flex;align-items:center;justify-content:space-around;padding:0 20px;font-size:12px;color:var(--dark)}
.register{top:60px;left:887px;width:151px;height:63px;background:var(--orange);color:#fff;font-size:14px;font-weight:500;display:flex;align-items:center;justify-content:center;box-shadow:0 4px 10px rgba(0,0,0,.2)}
.hero-title{top:246px;left:162px;font-size:51px;color:#fff}
.hero-sub{top:368px;left:162px;width:330px;font-size:14px;color:#fff;line-height:1.6}
.hero-btn{top:432px;left:162px;width:148px;height:34px;border:1px solid #fff;color:#fff;font-size:15px;display:flex;align-items:center;justify-content:center;gap:8px}
/* about */
.about-h{top:796px;left:162px;font-size:46px;font-weight:400}
.about-p{top:866px;left:162px;width:365px;font-size:12.5px;line-height:22px}
.ph{position:absolute}
/* stats */
.stats{top:1178px;left:0;width:1200px;height:373px;background:linear-gradient(90deg,#2f2f33,#5b5552 45%,#3d3a39 75%,#2a2a2c)}
.stat{position:absolute;width:240px;text-align:center;color:#fff}
.stat .icon{height:92px;display:flex;align-items:flex-end;justify-content:center}
.stat .num{font-family:var(--head);font-weight:600;font-size:38px;margin-top:10px;line-height:1.2}
.stat .lbl{font-size:17px;margin-top:2px}
/* why */
.why-h{top:1618px;left:162px;font-size:46px}
.why-h span{color:var(--orange)}
.why-p{top:1748px;left:162px;width:410px;font-size:11.5px;line-height:23px}
.cell{position:absolute;border:1px solid var(--line);text-align:center;padding:26px 12px 0}
.cell svg{width:36px;height:36px}
.cell h4{font-family:var(--head);font-weight:400;font-size:16px;color:var(--dark);margin:10px 0 12px;line-height:1.4}
.cell p{font-size:11px;line-height:19px;color:#777}
/* featured */
.featured{top:2235px;left:0;width:1200px;height:471px;background:linear-gradient(90deg,#4a4a4a,#6d6561 50%,#8a7a5a 80%,#4b4b4b)}
.course{position:absolute;top:2362px;width:276px;height:298px;background:#fff;overflow:hidden}
.course .img{height:186px}
.course h5{font-family:var(--head);font-weight:400;font-size:18px;color:var(--dark);margin:12px 0 0 24px}
.meta{display:flex;align-items:center;gap:14px;font-size:11px;color:#777;margin:10px 0 0 24px}
.meta svg{width:16px;height:16px}
.ring{position:absolute;right:-18px;bottom:-18px;width:58px;height:58px;border-radius:50%;border:12px solid var(--orange-soft)}
/* blog */
.blog{position:absolute;top:2856px;width:300px;height:301px;background:#fff;box-shadow:0 0 12px rgba(0,0,0,.12)}
.blog .img{position:absolute;top:10px;left:8px;width:284px;height:223px}
.blog h5{position:absolute;top:252px;left:22px;font-family:var(--head);font-weight:400;font-size:18px;color:var(--dark)}
.blog .date{position:absolute;top:258px;left:180px;display:flex;gap:8px;align-items:center;font-size:11px;color:#777}
/* newsletter */
.news{top:3232px;left:0;width:1200px;height:300px;background:var(--orange)}
/* footer */
.footer{top:4094px;left:0;width:1200px;height:292px;background:var(--orange);color:#fff}
.fh{position:absolute;top:71px;font-family:var(--head);font-weight:500;font-size:22px;color:#fff}
.flink{position:absolute;font-size:12px;color:#fff;display:flex;align-items:center;gap:8px}
.flink svg{width:6px;height:9px}
</style>
</head>
<body>

<!-- HERO -->
<section class="abs hero">
  <div class="hero-photo" role="img" aria-label="Students studying together at a table with a tablet"></div>
  <svg class="abs" style="inset:0" width="1200" height="599" viewBox="0 0 1200 599">
    <defs><linearGradient id="heroG" x1="0" x2="1"><stop offset="0" stop-color="#e5642f" stop-opacity=".95"/><stop offset="1" stop-color="#e85c2a" stop-opacity=".9"/></linearGradient></defs>
    <polygon points="0,0 752,0 385,599 0,599" fill="url(#heroG)"/>
  </svg>
  <div class="logo" style="top:16px;left:162px;width:204px">
    <div class="name">VORNA</div>
    <div class="sub">LEARNING CENTRE</div>
  </div>
  <nav class="abs nav"><span>HOME</span><span>BLOGS</span><span>COURSES</span><span>CONTACT US</span><span>ABOUT US</span><span>SIGN IN</span></nav>
  <svg class="abs" style="top:122px;left:436px" width="20" height="12"><polygon points="0,0 20,0 10,10" fill="#fff"/></svg>
  <div class="abs register">REGISTER</div>
  <h1 class="abs h hero-title">Privacy Learning<br>Excellence</h1>
  <p class="abs hero-sub">Largest online e-learning resource for data protection &amp; privacy</p>
  <div class="abs hero-btn">Get Training <svg width="8" height="10" viewBox="0 0 8 10"><path d="M2 1l4 4-4 4" stroke="#fff" fill="none" stroke-width="1.5"/></svg></div>
</section>

<!-- ABOUT -->
<h2 class="abs h about-h">About Us</h2>
<p class="abs about-p">Lorem Ipsum is simply dummy text of the printing and typesetting industry. Lorem Ipsum has been the industry's standard dummy text ever since the 1500s.Lorem Ipsum is simply dummy text of the printing and typesetting industry. Lorem Ipsum has been the industry's standard dummy text ever since the 1500s.</p>
<div class="btn-outline" style="top:1026px;left:162px;width:134px;height:34px">Learn More <svg viewBox="0 0 8 10"><path d="M2 1l4 4-4 4" stroke="#e85c2a" fill="none" stroke-width="1.5"/></svg></div>
<div class="ph" style="top:676px;left:739px;width:299px;height:335px;background:linear-gradient(135deg,#e06a38,#ef9a6e)" role="img" aria-label="Students in a library with an orange tint"></div>
<div class="ph" style="top:766px;left:650px;width:298px;height:335px;background:linear-gradient(140deg,#5a5656,#8a8077 50%,#3f4a5c)" role="img" aria-label="Student working on a laptop"></div>

<!-- STATS -->
<section class="abs stats" role="img" aria-label="Students with laptops in the background"></section>
<div class="stat" style="top:1268px;left:98px">
  <div class="icon"><svg width="112" height="86" viewBox="0 0 112 86"><path d="M6 8h38q12 0 12 10v64q0-8-12-8H6z M106 8H68q-12 0-12 10v64q0-8 12-8h38z" fill="none" stroke="#e85c2a" stroke-width="8"/></svg></div>
  <div class="num">114</div><div class="lbl">LESSONS</div>
</div>
<div class="stat" style="top:1268px;left:435px">
  <div class="icon"><svg width="90" height="92" viewBox="0 0 90 92"><rect x="6" y="16" width="78" height="70" rx="8" fill="#e85c2a"/><rect x="14" y="6" width="62" height="6" rx="3" fill="#e85c2a"/><polygon points="36,36 60,51 36,66" fill="#3a3737"/></svg></div>
  <div class="num">169</div><div class="lbl">VIDEOS</div>
</div>
<div class="stat" style="top:1268px;left:809px">
  <div class="icon"><svg width="112" height="86" viewBox="0 0 112 86"><polygon points="56,4 110,28 56,50 2,28" fill="#e85c2a"/><path d="M26 42v22q30 22 60 0V42L56 56z" fill="#e85c2a"/><rect x="98" y="30" width="4" height="26" fill="#e85c2a"/></svg></div>
  <div class="num">6,375</div><div class="lbl">ENROLLED STUDENTS</div>
</div>
<svg class="abs" style="top:1526px;left:160px" width="60" height="26" viewBox="0 0 60 26"><path d="M0 26Q30 -8 60 26z" fill="#fff"/><path d="M24 14l6 5 6-5" stroke="#2b2b2b" fill="none" stroke-width="2"/></svg>

<!-- WHY -->
<svg class="abs" style="top:1552px;left:1098px" width="102" height="170" viewBox="0 0 102 170"><circle cx="102" cy="85" r="70" fill="none" stroke="#f8dccf" stroke-width="30"/></svg>
<h2 class="abs h why-h">Why the <span>(Vorna)</span><br>Lerning Center?</h2>
<p class="abs why-p">Our mission at the Vorna Learning Centre is to provide business and job opportunities, as well as to enhance personal and career advancement for data protection / privacy professionals.</p>

<div class="cell" style="top:1702px;left:597px;width:222px;height:196px">
  <svg viewBox="0 0 36 36"><rect x="16" y="4" width="4" height="30" fill="#e85c2a"/><path d="M18 8h12l4 4-4 4H18z M18 14H6l-4 4 4 4h12z" fill="#e85c2a"/></svg>
  <h4>COMPREHENSIVE ROADMAP</h4><p>Our objective is to provide a comprehensive competency roadmap.....</p>
</div>
<div class="cell" style="top:1702px;left:819px;width:219px;height:196px">
  <svg viewBox="0 0 36 36"><rect x="7" y="7" width="22" height="22" fill="none" stroke="#e85c2a" stroke-width="2.5"/><g fill="#e85c2a"><rect x="3" y="3" width="8" height="8"/><rect x="25" y="3" width="8" height="8"/><rect x="3" y="25" width="8" height="8"/><rect x="25" y="25" width="8" height="8"/></g></svg>
  <h4>OPERATIONAL PERSPECTIVE</h4><p>We cover a broad range of data protection topics from both a legal ....</p>
</div>
<div class="cell" style="top:1898px;left:162px;width:218px;height:192px">
  <svg viewBox="0 0 36 36"><circle cx="18" cy="13" r="9" fill="none" stroke="#e85c2a" stroke-width="3"/><path d="M12 20l-4 13 6-3 3 5 1-14z M24 20l4 13-6-3-3 5-1-14z" fill="#e85c2a"/></svg>
  <h4>ACADEMIC &amp; INTERNATIONAL<br>CERTIFICATION</h4><p>We partner with prominent universities in the region as well as international certification..</p>
</div>
<div class="cell" style="top:1898px;left:380px;width:217px;height:192px">
  <svg viewBox="0 0 36 36"><g fill="#e85c2a"><circle cx="18" cy="18" r="4"/><circle cx="6" cy="10" r="3"/><circle cx="30" cy="10" r="3"/><circle cx="8" cy="28" r="3"/><circle cx="28" cy="28" r="3"/><circle cx="18" cy="4" r="2.5"/></g><path d="M18 18L6 10M18 18L30 10M18 18L8 28M18 18L28 28M18 18V4" stroke="#e85c2a" stroke-width="1.5"/></svg>
  <h4>NETWORK WITH OTHER<br>PEERS</h4><p>Participate in our online communities and rooms and your network with other....</p>
</div>
<div class="cell" style="top:1898px;left:597px;width:222px;height:192px">
  <svg viewBox="0 0 36 36"><path d="M4 10h8a4 4 0 1 1 8 0h8v8a4 4 0 1 1 0 8v8H4z" fill="#e85c2a"/></svg>
  <h4>MODULAR APPROACH &amp;<br>FLEXIBILITY</h4><p>All our courses are modular in nature to cater to the busy professional, meaning.....</p>
</div>
<div class="cell" style="top:1898px;left:819px;width:219px;height:192px">
  <svg viewBox="0 0 36 36"><path d="M13 10V6h10v4" fill="none" stroke="#e85c2a" stroke-width="2.5"/><rect x="3" y="10" width="30" height="22" rx="2" fill="#e85c2a"/><rect x="3" y="18" width="30" height="2" fill="#fff"/></svg>
  <h4>BUSINESS AND JOB<br>OPPORTUNITIES</h4><p>Collaborate with other professionals on potential business whether it relates to.....</p>
</div>
<div class="btn-outline" style="top:2122px;left:533px;width:133px;height:36px">Learn More <svg viewBox="0 0 8 10"><path d="M2 1l4 4-4 4" stroke="#e85c2a" fill="none" stroke-width="1.5"/></svg></div>

<!-- FEATURED COURSES -->
<section class="abs featured" role="img" aria-label="Students in a classroom in the background"></section>
<h2 class="abs h" style="top:2270px;left:0;width:1200px;text-align:center;font-size:50px;color:#fff">Featured Courses</h2>
<article class="course" style="left:162px">
  <div class="img" style="background:linear-gradient(135deg,#c9c9c9,#7a7a7a 60%,#d8b8a0)" role="img" aria-label="Laptop showing code on a desk"></div>
  <h5>How To Scale Social Imapct</h5>
  <div class="meta"><svg viewBox="0 0 16 16"><rect x="2" y="3" width="12" height="11" fill="none" stroke="#e85c2a" stroke-width="1.3"/><path d="M2 6h12M5 1v3M11 1v3" stroke="#e85c2a" stroke-width="1.3"/></svg>Dec 17, 2019</div>
  <div class="meta"><svg viewBox="0 0 16 16"><circle cx="8" cy="5" r="3.5" fill="none" stroke="#e85c2a" stroke-width="1.3"/><path d="M2 15q6-10 12 0" fill="none" stroke="#e85c2a" stroke-width="1.3"/></svg>Mr.Example</div>
  <div class="ring"></div>
</article>
<article class="course" style="left:461px">
  <div class="img" style="background:linear-gradient(135deg,#e9d8c8,#c8a48a 55%,#f0e4d8)" role="img" aria-label="Two students talking at a table"></div>
  <h5>Global Social Entrepreneurship</h5>
  <div class="meta"><svg viewBox="0 0 16 16"><rect x="2" y="3" width="12" height="11" fill="none" stroke="#e85c2a" stroke-width="1.3"/><path d="M2 6h12M5 1v3M11 1v3" stroke="#e85c2a" stroke-width="1.3"/></svg>Dec 18, 2019</div>
  <div class="meta"><svg viewBox="0 0 16 16"><circle cx="8" cy="5" r="3.5" fill="none" stroke="#e85c2a" stroke-width="1.3"/><path d="M2 15q6-10 12 0" fill="none" stroke="#e85c2a" stroke-width="1.3"/></svg>Mr.Example</div>
  <div class="ring"></div>
</article>
<article class="course" style="left:761px">
  <div class="img" style="background:linear-gradient(135deg,#8a7a6a,#c2a88e 50%,#5c5f6a)" role="img" aria-label="Two students holding books in a library"></div>
  <h5>Lumora Demonstration Course</h5>
  <div class="meta"><svg viewBox="0 0 16 16"><rect x="2" y="3" width="12" height="11" fill="none" stroke="#e85c2a" stroke-width="1.3"/><path d="M2 6h12M5 1v3M11 1v3" stroke="#e85c2a" stroke-width="1.3"/></svg>Dec 19, 2019</div>
  <div class="meta"><svg viewBox="0 0 16 16"><circle cx="8" cy="5" r="3.5" fill="none" stroke="#e85c2a" stroke-width="1.3"/><path d="M2 15q6-10 12 0" fill="none" stroke="#e85c2a" stroke-width="1.3"/></svg>Mr.Example</div>
  <div class="ring"></div>
</article>

<!-- LATEST BLOG -->
<h2 class="abs h" style="top:2770px;left:0;width:1200px;text-align:center;font-size:50px">Latest Blog</h2>
<article class="blog" style="left:277px">
  <div class="img" style="background:linear-gradient(135deg,#6b4a3a,#d8c4b4 55%,#f2ece6)" role="img" aria-label="Student reading a book at a desk"></div>
  <h5>How to write blog</h5>
  <div class="date"><svg width="16" height="16" viewBox="0 0 16 16"><rect x="2" y="3" width="12" height="11" fill="none" stroke="#e85c2a" stroke-width="1.3"/><path d="M2 6h12M5 1v3M11 1v3" stroke="#e85c2a" stroke-width="1.3"/></svg>Dec 18, 2019</div>
</article>
<article class="blog" style="left:623px">
  <div class="img" style="background:linear-gradient(180deg,#7a4a30,#a86a44 50%,#3e3a3a)" role="img" aria-label="Stack of books in front of bookshelves"></div>
  <h5>Hello world!</h5>
  <div class="date" style="left:180px"><svg width="16" height="16" viewBox="0 0 16 16"><rect x="2" y="3" width="12" height="11" fill="none" stroke="#e85c2a" stroke-width="1.3"/><path d="M2 6h12M5 1v3M11 1v3" stroke="#e85c2a" stroke-width="1.3"/></svg>Dec 19, 2019</div>
</article>

<!-- NEWSLETTER -->
<section class="abs news"></section>
<h2 class="abs h" style="top:3280px;left:162px;font-size:50px;color:#fff">Sign up our newsletter</h2>
<p class="abs" style="top:3354px;left:162px;width:570px;font-size:14px;line-height:23px;color:#fff">Subscribe now and receive weekly newsletter with educational materials, new courses, interesting posts, popular books and much more!</p>
<div class="abs" style="top:3448px;left:162px;width:391px;height:25px;border-bottom:1px solid #fff;font-size:13px;color:#fff">Enter your e-mail</div>
<svg class="abs" style="top:3448px;left:522px" width="22" height="20" viewBox="0 0 22 20"><path d="M1 9L21 1 15 19 11 12z" fill="#fff"/><path d="M11 12L21 1" stroke="#e85c2a" stroke-width="1"/></svg>
<div class="abs" style="top:3226px;left:800px;width:238px;height:306px;background:linear-gradient(180deg,#e8ddd6,#d4c8c0 60%,#8aa2bd)" role="img" aria-label="Student sitting cross-legged reading a book"></div>

<!-- TESTIMONIALS -->
<h2 class="abs h" style="top:3596px;left:0;width:1200px;text-align:center;font-size:50px">What People Say</h2>
<div class="abs" style="top:3682px;left:218px;width:148px;height:338px;background:var(--orange);border-radius:8px"></div>
<div class="abs" style="top:3719px;left:160px;width:264px;height:264px;background:#fff;box-shadow:0 0 10px rgba(0,0,0,.15)"></div>
<div class="abs" style="top:3741px;left:199px;width:187px;height:150px;background:linear-gradient(135deg,#7a8a7a,#e8e2da 50%,#e85c2a)" role="img" aria-label="Smiling student holding a folder in a library"></div>
<div class="abs" style="top:3920px;left:160px;width:264px;text-align:center;font-size:15px;color:var(--dark)">LOREM IPSUM</div>
<div class="abs" style="top:3944px;left:160px;width:264px;text-align:center;font-size:10px;font-style:italic">Lorem</div>
<svg class="abs" style="top:3772px;left:439px" width="48" height="38" viewBox="0 0 48 38"><path d="M2 38V22Q2 6 18 0v8Q10 12 10 18h10v20z M26 38V22Q26 6 42 0v8Q34 12 34 18h10v20z" fill="#6b6b6b"/></svg>
<p class="abs" style="top:3820px;left:500px;width:500px;font-size:11.5px;line-height:23px;font-style:italic">Defining dummy text<br>Its sole purpose is to fill out blank spaces with "word-like" content, without making any copyright infringements. Dummy text is also known as filler text or placeholder text, and it has been used for a long time in the various fields of online publishing</p>
<svg class="abs" style="top:3942px;left:500px" width="56" height="14" viewBox="0 0 56 14"><circle cx="7" cy="7" r="5" fill="#e85c2a"/><circle cx="27" cy="7" r="5" fill="none" stroke="#e85c2a" stroke-width="1.5"/><circle cx="47" cy="7" r="5" fill="#e85c2a"/></svg>
<svg class="abs" style="top:3926px;left:992px" width="48" height="38" viewBox="0 0 48 38"><path d="M46 0v16Q46 32 30 38v-8Q38 26 38 20H28V0z M22 0v16Q22 32 6 38v-8Q14 26 14 20H4V0z" fill="#6b6b6b"/></svg>

<!-- FOOTER -->
<footer class="abs footer">
  <div class="logo" style="top:56px;left:162px;width:188px">
    <div class="name" style="font-size:36px">VORNA</div>
    <div class="sub">LEARNING CENTRE</div>
  </div>
  <p class="abs" style="top:140px;left:162px;font-size:11px;line-height:19px">©VORNA Learning Center - 2020<br>All Rights Reserved.</p>

  <h3 class="fh" style="left:405px">QUICK LINKS</h3>
  <div class="flink" style="top:121px;left:405px"><svg viewBox="0 0 6 9"><path d="M1 1l3.5 3.5L1 8" stroke="#fff" fill="none" stroke-width="1.3"/></svg>Home</div>
  <div class="flink" style="top:148px;left:405px"><svg viewBox="0 0 6 9"><path d="M1 1l3.5 3.5L1 8" stroke="#fff" fill="none" stroke-width="1.3"/></svg>Blogs</div>
  <div class="flink" style="top:175px;left:405px"><svg viewBox="0 0 6 9"><path d="M1 1l3.5 3.5L1 8" stroke="#fff" fill="none" stroke-width="1.3"/></svg>Courses</div>
  <div class="flink" style="top:202px;left:405px"><svg viewBox="0 0 6 9"><path d="M1 1l3.5 3.5L1 8" stroke="#fff" fill="none" stroke-width="1.3"/></svg>Contact us</div>
  <div class="flink" style="top:121px;left:511px"><svg viewBox="0 0 6 9"><path d="M1 1l3.5 3.5L1 8" stroke="#fff" fill="none" stroke-width="1.3"/></svg>About us</div>
  <div class="flink" style="top:148px;left:511px"><svg viewBox="0 0 6 9"><path d="M1 1l3.5 3.5L1 8" stroke="#fff" fill="none" stroke-width="1.3"/></svg>Sign in</div>
  <div class="flink" style="top:175px;left:511px"><svg viewBox="0 0 6 9"><path d="M1 1l3.5 3.5L1 8" stroke="#fff" fill="none" stroke-width="1.3"/></svg>Register</div>

  <h3 class="fh" style="left:654px">CONTACT US</h3>
  <svg class="abs" style="top:118px;left:654px" width="14" height="18" viewBox="0 0 14 18"><path d="M7 18Q0 10 0 7a7 7 0 0 1 14 0q0 3-7 11z" fill="#fff"/><circle cx="7" cy="7" r="2.5" fill="#e85c2a"/></svg>
  <p class="abs" style="top:116px;left:683px;font-size:11px;line-height:18px">418 Harlow Bend, Ferncastle,<br>TX 75210, USA</p>
  <svg class="abs" style="top:172px;left:654px" width="16" height="16" viewBox="0 0 16 16"><path d="M3 1l3 3-2 2q2 4 6 6l2-2 3 3-2 2Q5 15 1 3z" fill="#fff"/></svg>
  <p class="abs" style="top:172px;left:683px;font-size:11px">+1 (800) 555 01 42</p>
  <svg class="abs" style="top:214px;left:654px" width="18" height="16" viewBox="0 0 18 16"><path d="M1 6L9 1l8 5v9H1z" fill="#fff"/><path d="M1 6l8 5 8-5" stroke="#e85c2a" fill="none" stroke-width="1.2"/></svg>
  <p class="abs" style="top:214px;left:683px;font-size:11px">support@study.vornaquill.com</p>

  <h3 class="fh" style="left:933px">FOLLOW US</h3>
  <svg class="abs" style="top:116px;left:920px" width="126" height="124" viewBox="0 0 126 124" role="img" aria-label="Social network links">
    <g fill="#f29a2e">
      <rect x="17" y="14" width="28" height="28" transform="rotate(45 31 28)"/>
      <rect x="80" y="14" width="28" height="28" transform="rotate(45 94 28)"/>
      <rect x="17" y="70" width="28" height="28" transform="rotate(45 31 84)"/>
      <rect x="80" y="70" width="28" height="28" transform="rotate(45 94 84)"/>
    </g>
  </svg>
</footer>

</body>
</html>
```